Flyer for tutoring

The text should be presented in an engaging way to attract potential customers.
Colorfully designed
Around the edge, various objects related to school and the subjects (see text) should be visible.

```html
<!DOCTYPE html>
<html lang="de">
<head>
<meta charset="utf-8">
<title>Nachhilfe Flyer</title>
<link rel="stylesheet" href="https://fonts.googleapis.com/css2?family=Lexend:wght@300;400;600;700;800&display=swap">
<style>
  :root {
    --violet: #4f16e8;
    --violet-deep: #3a0fb8;
    --pink: #ff0f8f;
    --gold: #f2b705;
    --lime: #d6e000;
    --sky: #12b8f2;
    --white: #ffffff;
    --ink: #1a1530;
    --paper: #f7f7f8;
  }
  * { margin: 0; padding: 0; box-sizing: border-box; }
  html, body { width: 895px; height: 1200px; overflow: hidden; background: #9aa6b6; }
  .flyer {
    position: relative; width: 895px; height: 1200px; overflow: hidden;
    font-family: "Lexend", sans-serif;
    background: linear-gradient(180deg, var(--violet) 0%, var(--violet-deep) 85%);
    color: var(--white);
  }
  .intro {
    position: absolute; top: 68px; left: 0; width: 100%; text-align: center;
    font-weight: 300; font-size: 29px; line-height: 40px;
  }
  .headline { position: absolute; top: 168px; left: 0; width: 100%; text-align: center; }
  .headline .pro { font-weight: 700; font-size: 46px; line-height: 56px; }
  .headline .badge {
    display: inline-block; font-weight: 800; letter-spacing: -1px;
    background: var(--white); border-radius: 14px; padding: 0 10px;
  }
  .headline .role1 { color: var(--pink); font-size: 56px; line-height: 64px; margin-top: 6px; }
  .headline .role2 { color: var(--gold); font-size: 56px; line-height: 60px; margin-top: -4px; }
  .tagline {
    position: absolute; top: 382px; left: 0; width: 100%; text-align: center;
    font-weight: 600; font-size: 21px;
  }
  .note {
    position: absolute; left: 156px; top: 465px; width: 582px; height: 155px;
    background: var(--lime); color: var(--ink);
    font-weight: 300; font-size: 16px; line-height: 21px; text-align: center;
    padding: 26px 30px 0 40px;
    clip-path: polygon(0 2%, 35% 0, 70% 3%, 100% 0, 99% 40%, 100% 75%, 98% 100%, 55% 98%, 20% 100%, 0 98%);
  }
  .note::before {
    content: ""; position: absolute; left: 8px; top: 10px; bottom: 10px;
    border-left: 5px dotted var(--violet);
  }
  .photo {
    position: absolute; left: 0; top: 606px; width: 292px; height: 364px;
    background: linear-gradient(180deg, #f2b705 0%, #1fa9e6 70%, #2a2a3a 100%);
    border-radius: 0 120px 0 0;
  }
  .lead {
    position: absolute; left: 333px; top: 648px; width: 380px;
    font-weight: 300; font-size: 16px; line-height: 21px;
  }
  .promise {
    position: absolute; left: 333px; top: 704px; width: 400px;
    font-weight: 800; font-size: 36px; line-height: 40px;
  }
  .promise span {
    background: var(--sky); padding: 0 6px; border-radius: 6px;
    box-decoration-break: clone; -webkit-box-decoration-break: clone;
  }
  .about {
    position: absolute; left: 334px; top: 845px; width: 450px;
    font-weight: 300; font-size: 15.5px; line-height: 19px;
  }
  .about strong { color: var(--lime); font-weight: 600; }
  .footer {
    position: absolute; left: 0; top: 970px; width: 100%; height: 230px;
    background: var(--paper); color: var(--ink);
  }
  .contact { position: absolute; left: 164px; top: 40px; font-size: 14px; }
  .contact h3 { font-weight: 600; font-size: 14px; margin-bottom: 8px; }
  .contact .row { display: flex; align-items: center; gap: 10px; font-weight: 300; font-size: 15px; }
  .contact .hint { margin-left: 20px; font-size: 12px; font-weight: 300; margin-bottom: 6px; }
  .contact svg { width: 12px; height: 12px; flex: none; }
  .farewell {
    position: absolute; left: 491px; top: 40px;
    font-weight: 300; font-size: 22px; line-height: 26px;
  }
</style>
</head>
<body>
<main class="flyer">
  <p class="intro">Möchtest du dich gerne in der<br>Schule verbessern und suchst eine</p>
  <div class="headline">
    <div class="pro">Professionelle</div>
    <div class="badge role1">NACHHILFELEHRERIN/</div><br>
    <div class="badge role2">LERNCOACH?</div>
  </div>
  <p class="tagline">Dann lass es uns doch mal versuchen!</p>

  <p class="note">Die erste Lektion – die Kennenlernlektion – dauert ca. 30 Minuten. Sie ist kostenlos. Denn wir müssen ja sicher gehen, dass wir uns verstehen und leiden können. Bei unserem ersten Treffen legen wir auch fest, woran wir arbeiten werden und wann die Nachhilfe in deine Agenda passt.</p>

  <div class="photo" role="img" aria-label="Foto eines lächelnden Schulkindes mit Rucksack und gelbem Buch"></div>

  <p class="lead">Wenn der erste Eindruck stimmt, dann legen wir los, und bald schon werden</p>
  <p class="promise"><span>deine Motivation und deine Noten besser und besser!</span></p>

  <p class="about"><strong>Zu meiner Person:</strong> Ich wohne hier in der Siedlung Lindenhof Wiesenstrasse und bin ausgebildete und sehr erfahrene Sekundar- und Primarlehrerin in den Fächern Deutsch, Französisch, Englisch und Geschichte. (Auf Wunsch auch Mathe-Nachhilfe möglich.)</p>

  <footer class="footer">
    <div class="contact">
      <h3>Meine Kontaktdaten:</h3>
      <div class="row">
        <svg viewBox="0 0 24 24"><path fill="#f2b705" d="M6.6 10.8a15 15 0 0 0 6.6 6.6l2.2-2.2a1 1 0 0 1 1-.25 11.4 11.4 0 0 0 3.6.57 1 1 0 0 1 1 1V20a1 1 0 0 1-1 1A17 17 0 0 1 3 4a1 1 0 0 1 1-1h3.5a1 1 0 0 1 1 1c0 1.25.2 2.45.57 3.57a1 1 0 0 1-.25 1z"/></svg>
        076 555 01 23
      </div>
      <div class="hint">(nachmittags fast immer erreichbar)</div>
      <div class="row">
        <svg viewBox="0 0 24 24"><path fill="#f2b705" d="M2 5h20v14H2z"/><path d="M2 5l10 8 10-8" fill="none" stroke="#fff" stroke-width="2"/></svg>
        lena.marti@example.com
      </div>
    </div>
    <p class="farewell">Ich freue mich auf<br>deine Kontaktaufnahme!<br>Bis bald!</p>
  </footer>
</main>
</body>
</html>
```